Brightmill Data Works

Our company is about IT hardwares and IT solutions. IT hardware such as PC, RAMS, storage and servers. IT solutions such as project management, BA. We are also selling new technology too.

Target Market(s)

Consumer, Small to Medium Business, Corporate

Requirements
Must have
• The business card must have the following:
• Name:
• Title:
• Contact Number:
• Email address:
• Website:
• Color: Must match the logo color upgrade

```html
<!DOCTYPE html>
<html lang="en">
<head>
<meta charset="utf-8">
<title>Brightmill Data Works – Business Card</title>
<link rel="stylesheet" href="https://fonts.googleapis.com/css2?family=Saira:wght@700&family=Arimo:wght@400;700&display=swap">
<style>
  :root {
    --backdrop: #1b1b1c;
    --card-top: #414143;
    --card-bottom: #323234;
    --ink-light: #e6e6e8;
    --ink-soft: #cfcfd2;
    --accent: #e08a1e;
  }
  * { margin: 0; padding: 0; box-sizing: border-box; }
  html, body {
    width: 1200px; height: 997px; overflow: hidden;
    background: var(--backdrop);
  }
  .stage {
    width: 1200px; height: 997px;
    display: flex; align-items: center; justify-content: center; gap: 60px;
  }
  .card {
    position: relative;
    width: 510px; height: 292px;
    border-radius: 18px;
    background: linear-gradient(160deg, var(--card-top), var(--card-bottom));
    box-shadow: 0 18px 40px rgba(0,0,0,.55);
    font-family: "Arimo", Arial, sans-serif;
  }
  .card-front {
    display: flex; flex-direction: column; align-items: center; justify-content: center; gap: 14px;
  }
  .brand-mark {
    width: 26px; height: 26px; border-radius: 50%;
    background: var(--accent);
  }
  .brand-name {
    font-family: "Saira", Arial, sans-serif; font-weight: 700;
    color: var(--ink-light);
    text-transform: uppercase; text-align: center;
    letter-spacing: 1px; line-height: 1.05;
  }
  .card-front .brand-name { font-size: 40px; }
  .card-back .brand-name {
    position: absolute; top: 44px; left: 0; right: 0;
    font-size: 34px;
  }
  .holder {
    position: absolute; left: 52px; bottom: 60px;
  }
  .holder-name {
    font-weight: 700; font-size: 19px; color: var(--accent);
    text-transform: uppercase; letter-spacing: .5px;
  }
  .holder-title {
    font-size: 14px; color: var(--ink-soft); margin-top: 4px; padding-left: 88px;
  }
  .divider {
    position: absolute; left: 286px; top: 158px;
    width: 2px; height: 76px;
    background: linear-gradient(to bottom, transparent, var(--accent), transparent);
  }
  .contacts {
    position: absolute; left: 310px; top: 160px;
    list-style: none; font-size: 13px; color: var(--ink-soft);
  }
  .contacts li { display: flex; align-items: center; gap: 8px; margin-bottom: 6px; }
  .contacts svg { width: 11px; height: 11px; fill: var(--accent); }
  .contacts .web {
    color: var(--accent); font-weight: 700; letter-spacing: 1.5px; padding-left: 19px;
  }
</style>
</head>
<body>
<main class="stage">
  <section class="card card-front" aria-label="Card front">
    <span class="brand-mark"></span>
    <h1 class="brand-name">Brightmill<br>Data Works</h1>
  </section>

  <section class="card card-back" aria-label="Card back">
    <h2 class="brand-name">Brightmill<br>Data Works</h2>
    <div class="holder">
      <p class="holder-name">Daniel Moreira</p>
      <p class="holder-title">Director</p>
    </div>
    <span class="divider"></span>
    <ul class="contacts">
      <li>
        <svg viewBox="0 0 24 24" aria-hidden="true"><path d="M6.6 10.8a15.1 15.1 0 0 0 6.6 6.6l2.2-2.2a1 1 0 0 1 1-.25 11.4 11.4 0 0 0 3.6.57 1 1 0 0 1 1 1V20a1 1 0 0 1-1 1A17 17 0 0 1 3 4a1 1 0 0 1 1-1h3.5a1 1 0 0 1 1 1c0 1.25.2 2.45.57 3.57a1 1 0 0 1-.25 1z"/></svg>
        <span>1441 555 0147</span>
      </li>
      <li>
        <svg viewBox="0 0 24 24" aria-hidden="true"><path d="M2 5h20v14H2z M2 5l10 8 10-8" /></svg>
        <span>dmoreira@brightmill.bm</span>
      </li>
      <li class="web">www.brightmill.bm</li>
    </ul>
  </section>
</main>
</body>
</html>
```